To design a brand identity that is simple and creative with 'Corvane' as the brand name, I like modern simple fonts like helvetica neue, I want to print both sides of the card, I am open to dark front and white back, but the design needs to transfer well to letter heads and email signatures, I am looking for sophisticated and elegant, but open minded about clever and off the wall, I do not do 'boring' Corvane Ventures is the mother company for a small group, specialising in Management & consulting, Software development and construction, we have a high level of integrity, we are transparent and accountable for what we do. my images are provided as a guide only, Im not expecting them to be just copied, Im looking for a creator and passionate thinker, who will put life into their work.

Target Market(s)

usually business minded people who are looking for something different in me, such as leadership, confidence and focus with thinking that is per haps a little outside the box..

Industry/Entity Type

Construction

Requirements
Must have
• clean, minmalistic
Nice to have
• custom logo
Should not have
• boring, traditional

```html
<!DOCTYPE html>
<html lang="en">
<head>
<meta charset="utf-8">
<title>Corvane business card</title>
<link href="https://fonts.googleapis.com/css2?family=Inter:wght@200;300;400&display=swap" rel="stylesheet">
<style>
  :root {
    --stage: #2f2c2a;
    --label: #e6e6e6;
    --front-plum: #673572;
    --front-magenta: #c41e5f;
    --back-light: #555352;
    --back-dark: #2c2c2c;
    --ink-light: #ffffff;
    --ink-soft: rgba(255,255,255,0.82);
    --mark: #e8644a;
    --accent-red: #d4262c;
  }
  * { margin: 0; padding: 0; box-sizing: border-box; }
  html, body { width: 1000px; height: 1200px; overflow: hidden; }
  body {
    background: var(--stage);
    font-family: "Inter", "Helvetica Neue", Arial, sans-serif;
    color: var(--ink-light);
    position: relative;
  }
  .set-label, .side-label {
    position: absolute;
    font-size: 19px;
    font-weight: 400;
    color: var(--label);
  }
  .set-label { left: 32px; top: 30px; }
  .side-label--front { left: 811px; top: 570px; color: #fff; }
  .side-label--back { left: 117px; top: 1143px; }

  .card {
    position: absolute;
    width: 740px;
    height: 457px;
    overflow: hidden;
  }

  /* Front */
  .card--front {
    left: 136px; top: 75px;
    background: linear-gradient(90deg, var(--front-plum) 0%, #8a2d6c 45%, var(--front-magenta) 100%);
  }
  .brand-lockup { position: absolute; left: 46px; top: 206px; }
  .brand-mark {
    position: absolute;
    border-radius: 50%;
    background: var(--mark);
  }
  .card--front .brand-mark { left: 0; top: 10px; width: 42px; height: 42px; }
  .card--front .brand-name {
    position: absolute; left: 88px; top: -4px;
    font-size: 52px; font-weight: 200; letter-spacing: 0.5px; line-height: 1;
  }
  .card--front .brand-tagline {
    position: absolute; left: 95px; top: 58px; white-space: nowrap;
    font-size: 13px; font-weight: 300; color: var(--ink-soft);
  }
  .divisions-vertical {
    position: absolute; left: 358px; top: 56px; height: 345px;
    writing-mode: vertical-rl; transform: rotate(180deg);
    font-size: 14.5px; font-weight: 300; letter-spacing: 1px;
    text-align: center; white-space: nowrap;
  }
  .brand-watermark {
    position: absolute; left: 334px; top: 102px; height: 260px;
    writing-mode: vertical-rl; transform: rotate(180deg);
    font-size: 80px; font-weight: 200; line-height: 1;
    color: rgba(255,255,255,0.2); white-space: nowrap;
  }
  .contact { position: absolute; left: 454px; top: 137px; }
  .contact__name { font-size: 26px; font-weight: 300; line-height: 1; }
  .contact__role { font-size: 16px; font-weight: 400; margin-top: 6px; }
  .contact__list { list-style: none; font-size: 18px; font-weight: 300; color: var(--ink-soft); margin-top: 10px; }
  .contact__list li { line-height: 28px; }
  .contact__list li.gap { margin-top: 13px; }

  /* Back */
  .card--back {
    left: 117px; top: 652px;
    background: radial-gradient(ellipse 60% 65% at 50% 28%, var(--back-light) 0%, #3e3d3c 55%, var(--back-dark) 100%);
  }
  .card--back .brand-mark { left: 150px; top: 184px; width: 96px; height: 96px; }
  .card--back .brand-name {
    position: absolute; left: 312px; top: 170px;
    font-size: 104px; font-weight: 200; line-height: 1; letter-spacing: 0.5px;
  }
  .divisions-row {
    position: absolute; left: 0; right: 0; top: 296px;
    text-align: center; font-size: 16px; font-weight: 300; letter-spacing: 1.4px;
  }
  .divisions-row .dot { color: var(--accent-red); margin: 0 6px; font-size: 12px; }
</style>
</head>
<body>
  <div class="set-label">Set 11</div>

  <section class="card card--front">
    <div class="brand-lockup">
      <span class="brand-mark"></span>
      <span class="brand-name">corvane</span>
      <span class="brand-tagline">… in the creation business</span>
    </div>
    <div class="brand-watermark">corvane</div>
    <div class="divisions-vertical">management • software • construction</div>
    <div class="contact">
      <div class="contact__name">Mara Lindqvist</div>
      <div class="contact__role">client ambassador</div>
      <ul class="contact__list">
        <li>c. +61 0438 512 904</li>
        <li>e. info@corvane.com.au</li>
        <li class="gap">a. po box 418 perth 6031</li>
        <li>w. www.corvane.ventures</li>
      </ul>
    </div>
  </section>
  <div class="side-label side-label--front">Front</div>

  <section class="card card--back">
    <span class="brand-mark"></span>
    <span class="brand-name">corvane</span>
    <div class="divisions-row">management<span class="dot">●</span>software<span class="dot">●</span>construction</div>
  </section>
  <div class="side-label side-label--back">Back</div>
</body>
</html>
```